NEW Wordpress Website Design for a Dynamic Long Term Healthcare Company in Hawaii

I would like a new website design for my current company, Marlow Health Collective, which has two different brands - Marlow Homecare and Marlow Senior Living. You can see the current website at www.marlowhealth-example.com. The website should be built using Wordpress Software and the Framewise theme. The website should have a local Hawaii island/tropical feel, but look professional for healthcare. I'm looking for something fresh, and want the designer to select colors, styles, etc.

In the Header, on all pages, I would like a menu that includes Home Care, Senior Living, Rates, and About Us.
Under each of the Header Menu Titles, I would like these drop downs included:
Home Care (drop down pages)- Nurse Aide Care, 24-Hour Home Care, Skilled Nursing, Lifestyle Aide, Hospice at Home, Bathing & Meal Service.
Senior Living (drop down pages) - Long-Term Stay, Short-Term Stay.
Rates (drop down page) - Rates.
About Us (drop down pages) - Our Mission, Ohana Talk, About Dana Marlow.

In the footer, on all pages, you should include the address: 248 Pueo Lane, Suite 310, Honolulu, HI 96817. Phone number: 808-555-0172
The footer should also include buttons for a page called Learn, Caregiver Jobs, and each of the service page links to include: Nurse Aide Care, 24-Hour Home Care, Skilled Nursing, Lifestyle Aide, Hospice at Home, Bathing & Meal Service.
Please don't take the current website and redesign a few aspects. I'm looking for a completely different look and feel.

Target Market(s)

40-80 year olds

Industry/Entity Type

Long Term Healthcare

Coding

Coded - Design and coding required

Requirements
Should not have
• Our existing website as a template. We are looking for a complete redesign. Thank you.

```html
<!DOCTYPE html>
<html lang="en">
<head>
<meta charset="utf-8">
<title>Marlow Health Collective</title>
<link href="https://fonts.googleapis.com/css2?family=Poppins:wght@400;500;600;700&family=EB+Garamond:wght@500;600&display=swap" rel="stylesheet">
<style>
:root{
  --teal:#2e6e66;
  --teal-dark:#245a53;
  --orange:#f4682a;
  --yellow:#f9b90c;
  --navy:#0e2a47;
  --ink:#1c1c1c;
  --muted:#4a4a4a;
  --peach:#f3dcd3;
  --mint:#d4e9e4;
  --line:#ececec;
  --gold:#f5a524;
}
*{box-sizing:border-box;margin:0;padding:0}
html,body{width:1200px;height:4054px;overflow:hidden}
body{position:relative;background:#fff;font-family:"Poppins",sans-serif;color:var(--ink)}
.abs{position:absolute}
.serif{font-family:"EB Garamond",serif}

/* hero */
.hero{left:0;top:0;width:1200px;height:539px;background:linear-gradient(180deg,#eef4f8 0%,#f6f8f9 45%,#e8ecea 70%,#d9dcd6 100%)}
.brand{left:142px;top:20px;display:flex;align-items:center;gap:10px;font-family:"EB Garamond",serif;font-weight:600;font-size:25px;color:var(--teal);line-height:1}
.brand .mark{width:22px;height:22px;background:var(--teal);border-radius:4px}
.nav{top:33px;left:529px;display:flex;gap:0;font-size:13px;font-weight:500}
.nav a{position:absolute;white-space:nowrap;color:var(--ink);text-decoration:none;display:flex;align-items:center;gap:5px}
.btn-contact{left:945px;top:22px;width:113px;height:41px;border-radius:21px;background:var(--orange);color:#fff;font-size:13px;font-weight:500;display:flex;align-items:center;justify-content:center}
.hero h1{left:142px;top:200px;font-weight:400;font-size:44px;line-height:55px;color:var(--ink)}
.hero h1 span{color:var(--orange);font-weight:600}
.hero p{left:142px;top:333px;width:420px;font-size:12.5px;line-height:21px;color:var(--ink)}
.btn-start{left:142px;top:400px;width:115px;height:40px;border-radius:20px;background:var(--yellow);font-size:12.5px;font-weight:600;display:flex;align-items:center;justify-content:center}
.hero-phone{left:277px;top:409px;font-size:14.5px;font-weight:600;display:flex;align-items:center;gap:10px}

/* services */
.photo{border-radius:50%;overflow:hidden}
.svc-label{width:400px;text-align:center;font-size:25px;font-weight:600;color:var(--teal);letter-spacing:.5px}

/* care band */
.care-photo{left:0;top:1181px;width:598px;height:462px;border-radius:0 40px 40px 0;background:linear-gradient(135deg,#5b7d3a 0%,#9aa86c 35%,#b9a9c6 55%,#8fa3b7 80%,#4e6a3b 100%)}
.care-card{top:1240px;width:267px;height:345px;background:var(--teal);border-radius:26px;color:#fff;text-align:center;padding:30px 12px 0}
.care-card h3{font-family:"EB Garamond",serif;font-weight:600;font-size:19px;line-height:25px;letter-spacing:.5px}
.care-card p{font-size:12.3px;line-height:21.5px;margin-top:10px}
.care-card .btn{position:absolute;left:20px;right:20px;top:275px;height:47px;border-radius:24px;background:#fff;color:var(--ink);font-size:12px;font-weight:600;display:flex;align-items:center;justify-content:center}

/* about */
.about h2{left:639px;top:1800px;font-size:26px;font-weight:600;color:var(--teal);letter-spacing:.5px}
.about p{left:639px;top:1848px;width:420px;font-size:14px;line-height:24px;color:var(--ink)}
.btn-read{left:636px;top:2036px;width:169px;height:49px;border:1.5px solid var(--teal);border-radius:25px;color:var(--teal);font-size:14px;font-weight:600;display:flex;align-items:center;justify-content:center}

/* testimonials */
.testi{left:0;top:2186px;width:1200px;height:465px;background:var(--teal)}
.testi h2{left:0;width:1200px;top:2220px;text-align:center;color:#fff;font-size:28px;font-weight:500}
.testi .sub{left:300px;width:600px;top:2262px;text-align:center;color:#fff;font-size:13.5px;line-height:24px}
.t-card{top:2336px;width:290px;height:256px;background:#fff;border-radius:10px;overflow:hidden}
.t-card h4{position:absolute;left:32px;top:26px;font-family:"EB Garamond",serif;font-weight:500;font-size:19px;color:var(--teal)}
.t-card p{position:absolute;left:31px;top:70px;width:235px;font-size:13.5px;line-height:24px;color:var(--muted)}
.t-card .foot{position:absolute;left:0;bottom:0;width:100%;height:72px;background:#e3efed}
.t-card .ava{position:absolute;left:36px;top:196px;width:42px;height:42px;border-radius:50%}
.t-card .who{position:absolute;left:90px;top:203px;font-size:12px;line-height:17px;color:var(--ink)}
.t-card .who b{font-weight:600}
.t-card .q{position:absolute;left:218px;top:168px}

/* form */
.form-title{left:0;width:1200px;top:2738px;text-align:center;font-size:27px;line-height:36px;font-weight:600;color:var(--teal);letter-spacing:.5px}
.form-panel{left:142px;top:2835px;width:916px;height:809px;background:#fff;box-shadow:0 2px 14px rgba(0,0,0,.08)}
.lbl{left:211px;font-size:12px;font-weight:600;color:var(--ink)}
.field{left:211px;width:778px;border:1px solid var(--line);border-radius:4px;background:#fff}
.chev{position:absolute;right:20px;top:50%;margin-top:-4px}
.agree{left:214px;top:3508px;font-size:13.5px;color:var(--ink)}
.btn-submit{left:517px;top:3569px;width:167px;height:46px;border:1px solid var(--line);border-radius:23px;color:var(--teal);font-size:13.5px;font-weight:600;display:flex;align-items:center;justify-content:center}

/* footer */
.footer{left:0;top:3695px;width:1200px;height:359px;background:linear-gradient(160deg,#0e2a47 0%,#183b56 55%,#22474f 100%)}
.f-brand{left:142px;top:3800px;display:flex;align-items:center;gap:16px;color:#fff;font-family:"EB Garamond",serif;font-weight:600;font-size:56px;line-height:1}
.f-brand .mark{width:44px;height:44px;background:#fff;border-radius:6px}
.f-col h5{font-size:16px;font-weight:600;color:var(--gold)}
.f-col a{display:block;color:#fff;font-size:12.5px;text-decoration:none;margin-top:10px;line-height:17.5px}
.f-contact{left:852px;top:3805px;color:#fff;font-size:12.5px;line-height:20px}
.f-rule{left:142px;top:3996px;width:916px;height:1px;background:rgba(255,255,255,.2)}
.copy{left:142px;top:4019px;color:#fff;font-size:12.5px}
.social{top:4014px;width:28px;height:28px;border-radius:50%;border:2px solid #fff}
</style>
</head>
<body>

<!-- HERO -->
<div class="abs hero" role="img" aria-label="Soft coastal background of a tropical beach with palm trees and pale sky"></div>
<svg class="abs" style="left:0;top:0" width="1200" height="539" aria-hidden="true">
  <path d="M0 150 Q80 230 60 330 Q40 420 0 440 Z" fill="#f3c7b6" opacity=".75"/>
  <path d="M0 140 Q90 230 70 330 Q50 430 0 450" fill="none" stroke="#e9b3a1" stroke-dasharray="3 4"/>
  <circle cx="192" cy="148" r="6" fill="#f7c84a"/>
  <circle cx="91" cy="219" r="12" fill="#9fc6d9"/>
  <polygon points="547,146 557,166 537,166" fill="#f4682a"/>
  <circle cx="643" cy="334" r="20" fill="#f9b90c"/>
  <circle cx="496" cy="436" r="12" fill="#f3c3b5"/>
  <circle cx="1109" cy="460" r="30" fill="#1d6b80"/>
  <circle cx="896" cy="315" r="181" fill="none" stroke="#555" stroke-width="1.5" stroke-dasharray="6 5"/>
</svg>
<div class="abs photo" style="left:731px;top:150px;width:330px;height:330px;background:linear-gradient(135deg,#d7e1e6 0%,#4e7fa6 40%,#a88b72 70%,#5a6b7a 100%)" role="img" aria-label="Caregiver in blue scrubs standing beside a smiling senior woman with a walker"></div>
<svg class="abs" style="left:868px;top:287px" width="56" height="56" aria-hidden="true">
  <circle cx="28" cy="28" r="28" fill="#fff" opacity=".9"/><circle cx="28" cy="28" r="19" fill="#f4682a"/>
  <polygon points="24,20 36,28 24,36" fill="#fff"/>
</svg>
<div class="abs photo" style="left:776px;top:113px;width:52px;height:52px;background:linear-gradient(135deg,#c9b09a,#6f7f7a);border:3px solid #fff" role="img" aria-label="Portrait of a senior man"></div>
<div class="abs photo" style="left:739px;top:448px;width:52px;height:52px;background:linear-gradient(135deg,#d6c0a8,#8a7b6a);border:3px solid #fff" role="img" aria-label="Portrait of a smiling senior man"></div>
<div class="abs photo" style="left:1028px;top:183px;width:44px;height:44px;background:linear-gradient(135deg,#e6ece9,#9bb3a8);border:3px solid #fff" role="img" aria-label="Portrait of a nurse"></div>

<div class="abs brand"><span class="mark"></span>Marlow</div>
<nav>
  <a class="abs nav" style="left:529px;top:34px">Home Care <svg width="9" height="6"><path d="M1 1l3.5 3.5L8 1" stroke="#1c1c1c" fill="none" stroke-width="1.3"/></svg></a>
  <a class="abs nav" style="left:644px;top:34px">Senior Living <svg width="9" height="6"><path d="M1 1l3.5 3.5L8 1" stroke="#1c1c1c" fill="none" stroke-width="1.3"/></svg></a>
  <a class="abs nav" style="left:767px;top:34px">Rates <svg width="9" height="6"><path d="M1 1l3.5 3.5L8 1" stroke="#1c1c1c" fill="none" stroke-width="1.3"/></svg></a>
  <a class="abs nav" style="left:846px;top:34px">About Us <svg width="9" height="6"><path d="M1 1l3.5 3.5L8 1" stroke="#1c1c1c" fill="none" stroke-width="1.3"/></svg></a>
</nav>
<div class="abs btn-contact">Contact Us</div>

<section class="hero-copy">
  <h1 class="abs" style="left:142px;top:200px;font-weight:400;font-size:44px;line-height:55px">Happiness Is A Cigar<br>Called <span style="color:var(--orange);font-weight:600">Senior Care</span></h1>
  <p class="abs" style="left:142px;top:333px;width:420px;font-size:12.5px;line-height:21px">Marlow Homecare provides a variety of professional in-home health care services throughout the entire island of Oahu.</p>
  <div class="abs btn-start">Get Started</div>
  <div class="abs hero-phone"><svg width="16" height="16" viewBox="0 0 24 24"><path d="M6.6 10.8a15 15 0 006.6 6.6l2.2-2.2a1 1 0 011-.25 11.4 11.4 0 003.6.57 1 1 0 011 1V20a1 1 0 01-1 1A17 17 0 013 4a1 1 0 011-1h3.5a1 1 0 011 1c0 1.25.2 2.45.57 3.57a1 1 0 01-.25 1z" fill="#1d6b80"/></svg>(808) 555-0172</div>
</section>

<!-- SERVICES -->
<svg class="abs" style="left:130px;top:655px" width="470" height="400" aria-hidden="true">
  <ellipse cx="110" cy="170" rx="100" ry="75" fill="var(--mint)"/>
  <ellipse cx="190" cy="110" rx="110" ry="105" fill="var(--peach)"/>
  <ellipse cx="330" cy="260" rx="95" ry="95" fill="#f0d3c8"/>
  <ellipse cx="290" cy="320" rx="90" ry="65" fill="var(--mint)"/>
</svg>
<div class="abs photo" style="left:200px;top:705px;width:330px;height:330px;background:linear-gradient(135deg,#d9d05c 0%,#c8c36a 40%,#6f8fb0 65%,#c29c7a 100%)" role="img" aria-label="Home caregiver smiling and helping a senior man adjust his shirt"></div>
<div class="abs svc-label serif" style="left:165px;top:1064px">HOMECARE</div>

<svg class="abs" style="left:623px;top:655px" width="470" height="400" aria-hidden="true">
  <ellipse cx="110" cy="170" rx="100" ry="75" fill="var(--mint)"/>
  <ellipse cx="190" cy="110" rx="110" ry="105" fill="var(--peach)"/>
  <ellipse cx="330" cy="260" rx="95" ry="95" fill="#f0d3c8"/>
  <ellipse cx="290" cy="320" rx="90" ry="65" fill="var(--mint)"/>
</svg>
<div class="abs photo" style="left:693px;top:705px;width:330px;height:330px;background:linear-gradient(135deg,#8fb38a 0%,#c84640 40%,#4b8fd6 65%,#5e6a55 100%)" role="img" aria-label="Caregiver assisting a senior man with light hand weights"></div>
<div class="abs svc-label serif" style="left:658px;top:1064px">SENIOR LIVING</div>

<!-- CARE BAND -->
<div class="abs care-photo" role="img" aria-label="Smiling woman with a walker and a male caregiver in scrubs among tropical plants"></div>
<div class="abs care-card" style="left:482px">
  <h3>PROFESSIONAL CARE<br>IN YOUR HOME</h3>
  <p>Marlow Homecare understands that every person's care journey is unique. We tailor our in-home services to meet the diverse nurturing experience of professional quality care and safety within the comfort and convenience of your own home.</p>
  <div class="btn">SCHEDULE CARE ASSESSMENT</div>
</div>
<div class="abs care-card" style="left:791px">
  <h3>TRUSTED CARE<br>IN OUR HOME</h3>
  <p>Marlow Senior Living creates a warm, supportive, and enriching care home environment where seniors can thrive in their golden years. We provide residential care that promotes well-being, connection, and dignity of each individual.</p>
  <div class="btn">SCHEDULE TOUR</div>
</div>

<!-- ABOUT -->
<svg class="abs" style="left:130px;top:1710px" width="470" height="400" aria-hidden="true">
  <ellipse cx="110" cy="170" rx="100" ry="75" fill="var(--mint)"/>
  <ellipse cx="190" cy="110" rx="110" ry="105" fill="var(--peach)"/>
  <ellipse cx="330" cy="260" rx="95" ry="95" fill="#f0d3c8"/>
  <ellipse cx="290" cy="320" rx="90" ry="65" fill="var(--mint)"/>
</svg>
<div class="abs photo" style="left:200px;top:1760px;width:330px;height:330px;background:linear-gradient(135deg,#cfd9c8 0%,#b04a83 35%,#9e3a44 55%,#7fbfae 75%,#d9c47a 100%)" role="img" aria-label="Three women sitting on a sofa knitting together"></div>
<section class="about">
  <h2 class="abs serif">ABOUT MARLOW HOMECARE</h2>
  <p class="abs">At Marlow Health Collective, our mission is to provide compassionate and professional long-term healthcare services that empower individuals to maintain their highest level of independence, health, and well-being in the comfort of their own homes or ours, either through our licensed home healthcare agency - Marlow Homecare, or in our Adult Residential Care Home - Marlow Senior Living.</p>
  <div class="abs btn-read">Read More</div>
</section>

<!-- TESTIMONIALS -->
<div class="abs testi"></div>
<h2 class="abs serif" style="left:0;width:1200px;top:2220px;text-align:center;color:#fff;font-size:28px;font-weight:500">Our Testimonials</h2>
<p class="abs" style="left:300px;width:600px;top:2262px;text-align:center;color:#fff;font-size:13.5px;line-height:24px">Herzlich Willkommen auf der Internetpräsentation des bundesweiten ambulanten Intensivpflegedienst Hana Pflege GmbH.</p>

<div class="abs t-card" style="left:142px">
  <h4>There are many variations</h4>
  <p>Lorem ipsum dolor sit amet &nbsp;con sectetuer adipiscing elit, seddi am nonummy nibh euismod tincidunt ut laoreet.</p>
  <div class="foot"></div>
  <svg class="q" width="40" height="34" aria-hidden="true"><path d="M3 32V16Q3 6 14 3M12 16H3M22 32V16Q22 6 33 3M31 16H22M3 32H12V16M22 32H31V16" fill="none" stroke="#777" stroke-width="1.3"/></svg>
  <div class="ava" style="background:linear-gradient(135deg,#8a6a52,#3b3b3b)" role="img" aria-label="Portrait of reviewer"></div>
  <div class="who"><b>JOHN JAMES</b><br>Leben für Hana Pflege GmbH</div>
</div>
<div class="abs t-card" style="left:455px">
  <h4>There are many variations</h4>
  <p>Lorem ipsum dolor sit amet &nbsp;con sectetuer adipiscing elit, seddi am nonummy nibh euismod tincidunt ut laoreet.</p>
  <div class="foot"></div>
  <svg class="q" width="40" height="34" aria-hidden="true"><path d="M3 32V16Q3 6 14 3M12 16H3M22 32V16Q22 6 33 3M31 16H22M3 32H12V16M22 32H31V16" fill="none" stroke="#777" stroke-width="1.3"/></svg>
  <div class="ava" style="background:linear-gradient(135deg,#d9c2b0,#5a4a40)" role="img" aria-label="Portrait of reviewer"></div>
  <div class="who"><b>DOE JAMES</b><br>Hana Pflege GmbH</div>
</div>
<div class="abs t-card" style="left:769px">
  <h4>There are many variations</h4>
  <p>Lorem ipsum dolor sit amet &nbsp;con sectetuer adipiscing elit, seddi am nonummy nibh euismod tincidunt ut laoreet.</p>
  <div class="foot"></div>
  <svg class="q" width="40" height="34" aria-hidden="true"><path d="M3 32V16Q3 6 14 3M12 16H3M22 32V16Q22 6 33 3M31 16H22M3 32H12V16M22 32H31V16" fill="none" stroke="#777" stroke-width="1.3"/></svg>
  <div class="ava" style="background:linear-gradient(135deg,#e0c0b0,#5a2f28)" role="img" aria-label="Portrait of reviewer"></div>
  <div class="who"><b>ALINA JAMES</b><br>Hana Pflege GmbH</div>
</div>

<!-- FORM -->
<h2 class="abs serif form-title">SCHEDULE A COMPLIMENTARY<br>CARE CONSULTATION</h2>
<div class="abs form-panel"></div>
<div class="abs lbl" style="top:2866px">Name*</div>
<div class="abs field" style="top:2890px;height:43px"></div>
<div class="abs lbl" style="top:2954px">Email*</div>
<div class="abs field" style="top:2978px;height:42px"></div>
<div class="abs lbl" style="top:3042px">Phone*</div>
<div class="abs field" style="top:3066px;height:42px"></div>
<div class="abs lbl" style="top:3129px">How can we help?</div>
<div class="abs field" style="top:3153px;height:42px"><svg class="chev" width="12" height="8"><path d="M1 1l5 5 5-5" stroke="#999" fill="none" stroke-width="1.2"/></svg></div>
<div class="abs lbl" style="top:3215px">Your Comments*</div>
<div class="abs field" style="top:3240px;height:77px"></div>
<div class="abs lbl" style="top:3338px">How did you hear about us?</div>
<div class="abs field" style="top:3363px;height:40px"></div>
<div class="abs lbl" style="top:3426px">May We Email You About This?</div>
<div class="abs field" style="top:3451px;height:41px"><svg class="chev" width="12" height="8"><path d="M1 1l5 5 5-5" stroke="#999" fill="none" stroke-width="1.2"/></svg></div>
<div class="abs agree">You agree to receive future emails and understand you may opt-out at any time</div>
<div class="abs btn-submit">SUBMIT</div>

<!-- FOOTER -->
<div class="abs footer" role="img" aria-label="Dark navy backdrop with faint palm tree silhouettes"></div>
<div class="abs f-brand"><span class="mark"></span>Marlow</div>
<div class="abs f-col" style="left:476px;top:3754px">
  <h5>Quick Links</h5>
  <a>Home Care</a><a>Senior Living</a><a>Rates</a><a>About Us</a><a>Caregiver Jobs</a>
</div>
<div class="abs f-col" style="left:658px;top:3754px">
  <h5>Resources</h5>
  <a>Privacy Policy</a><a>Terms Of Service</a><a>Contact Us</a>
</div>
<div class="abs f-col" style="left:852px;top:3754px"><h5>Contact Info</h5></div>
<div class="abs f-contact" style="left:852px;top:3800px;display:flex;gap:10px">
  <svg width="16" height="20" viewBox="0 0 24 30"><path d="M12 1a9 9 0 00-9 9c0 7 9 18 9 18s9-11 9-18a9 9 0 00-9-9z" fill="none" stroke="#f5a524" stroke-width="2.4"/><circle cx="12" cy="10" r="3.2" fill="#f5a524"/></svg>
  <span>248 Pueo Lane, Suite 310,<br>Honolulu, HI 96817</span>
</div>
<div class="abs f-contact" style="left:852px;top:3850px;display:flex;gap:10px;align-items:center">
  <svg width="16" height="16" viewBox="0 0 24 24"><path d="M6.6 10.8a15 15 0 006.6 6.6l2.2-2.2a1 1 0 011-.25 11.4 11.4 0 003.6.57 1 1 0 011 1V20a1 1 0 01-1 1A17 17 0 013 4a1 1 0 011-1h3.5a1 1 0 011 1c0 1.25.2 2.45.57 3.57a1 1 0 01-.25 1z" fill="#f5a524"/></svg>
  <span>808-555-0172</span>
</div>
<div class="abs f-rule"></div>
<div class="abs copy">© 2024 Marlow Health Collective. All Rights Reserved.</div>
<div class="abs social" style="left:925px" aria-label="Social link"></div>
<div class="abs social" style="left:961px" aria-label="Social link"></div>
<div class="abs social" style="left:996px" aria-label="Social link"></div>
<div class="abs social" style="left:1031px" aria-label="Social link"></div>

</body>
</html>
```